Tobias Ränkel and Co stationary design

Name of business:
Tobias Ränkel and Co

Can be written as:
Tobias Ränkel and Co
Tobias Ränkel & Co
tobias ränkel & co

If broken into letters:
TR&Co
tr&co

We are a Railway Safety Training Company
Our focus is on rail safety, Rail Management, Safety Management, Train Control Training, Accident Investigation.

.

Project Deadline Extended Reason: The original date was set to commence as soon as the logo contest finished. Sketch harbor started the project as soon as it was paid. Added Thursday, May 12, 2016

Target Market(s)

Professionals, CEO's and Managing Directors

Industry/Entity Type

Management Consulting

Font styles to use
Sans Serif

Requirements
Must have
• Professional, Sharp, Creative and modern
• Please note that this is for stationary concept which must include
• - business card
• - letterhead
• - envelope
• - with compliments slip
• - document cover (like book or folder cover)
• - dividers for folders....
• These must all have a common theme or style
Nice to have
• Keep if fresh
Should not have
• Please don't sent just fonts.... Must be creative

```html
<!DOCTYPE html>
<html lang="en">
<head>
<meta charset="utf-8">
<title>Tobias Ränkel &amp; Co — Business Card</title>
<link rel="stylesheet" href="https://fonts.googleapis.com/css2?family=Open+Sans:wght@400;600;700&display=swap">
<style>
  :root {
    --navy: #1c2f66;
    --navy-deep: #14234f;
    --navy-light: #2c4386;
    --red: #d8203a;
    --white: #ffffff;
    --paper: #eceae6;
    --rule: #8e9bc3;
  }
  * { margin: 0; padding: 0; box-sizing: border-box; }
  html, body { width: 1200px; height: 843px; overflow: hidden; }
  body {
    background: var(--paper);
    font-family: "Open Sans", Arial, sans-serif;
    position: relative;
  }
  .card {
    position: absolute;
    width: 540px;
    height: 309px;
    top: 267px;
    border-radius: 3px;
    overflow: hidden;
    box-shadow: 0 6px 18px rgba(0,0,0,.18);
  }
  .card--back {
    left: 40px;
    background: radial-gradient(ellipse at 45% 45%, var(--navy-light) 0%, var(--navy) 55%, var(--navy-deep) 100%);
    color: var(--white);
    text-align: center;
  }
  .back__name {
    position: absolute;
    left: 0; right: 0; top: 122px;
    font-size: 28px;
    font-weight: 700;
    line-height: 36px;
    letter-spacing: .5px;
  }
  .back__web {
    position: absolute;
    left: 0; right: 0; top: 164px;
    font-size: 12px;
    line-height: 16px;
    letter-spacing: 5px;
  }
  .card--front { left: 620px; background: var(--white); }
  .front__shapes { position: absolute; inset: 0; }
  .front__brand {
    position: absolute;
    left: 0; right: 0; top: 78px;
    display: flex; justify-content: center; align-items: center; gap: 12px;
    color: var(--navy);
    font-size: 26px; font-weight: 700; line-height: 34px;
  }
  .front__brand-dot {
    width: 20px; height: 20px; border-radius: 50%;
    background: var(--red);
  }
  .front__person {
    position: absolute; left: 0; right: 0; top: 196px;
    text-align: center; color: var(--white);
    font-size: 15px; font-weight: 600; line-height: 20px; letter-spacing: .3px;
  }
  .front__person-role { font-weight: 400; font-size: 13px; }
  .contact {
    position: absolute; color: var(--white);
    font-size: 12.5px; line-height: 18px; white-space: nowrap;
  }
  .contact--address { left: 20px; top: 222px; }
  .contact--phones { left: 196px; top: 236px; }
  .contact--office { left: 366px; top: 250px; }
  .contact__row { display: flex; align-items: center; gap: 7px; }
  .contact__row svg { width: 12px; height: 12px; fill: var(--white); flex: none; }
</style>
</head>
<body>

<section class="card card--back" aria-label="Business card back">
  <div class="back__name">Tobias Ränkel &amp; Co.</div>
  <div class="back__web">www.rankelco.com</div>
</section>

<section class="card card--front" aria-label="Business card front">
  <svg class="front__shapes" viewBox="0 0 540 309" preserveAspectRatio="none" aria-hidden="true">
    <path d="M150,0 H540 V34 Q360,2 150,0 Z" fill="var(--red)"/>
    <path d="M0,168 Q270,212 540,176 V309 H0 Z" fill="var(--navy)"/>
    <line x1="18" y1="191" x2="522" y2="191" stroke="var(--rule)" stroke-width="1"/>
    <line x1="18" y1="294" x2="522" y2="294" stroke="var(--rule)" stroke-width="1"/>
  </svg>

  <div class="front__brand">
    <div class="front__brand-dot"></div>
    <div class="front__brand-name">TR &amp; Co.</div>
  </div>

  <div class="front__person">MARCUS HALE - <span class="front__person-role">CEO/FOUNDER</span></div>

  <div class="contact contact--address">
    <div>4218 Linden Crest</div>
    <div>Juneau, Alaska 36821</div>
  </div>

  <div class="contact contact--phones">
    <div class="contact__row">
      <svg viewBox="0 0 24 24"><path d="M6.6 10.8a15 15 0 0 0 6.6 6.6l2.2-2.2a1 1 0 0 1 1-.25 11.4 11.4 0 0 0 3.6.57 1 1 0 0 1 1 1V20a1 1 0 0 1-1 1A17 17 0 0 1 3 4a1 1 0 0 1 1-1h3.5a1 1 0 0 1 1 1c0 1.25.2 2.45.57 3.57a1 1 0 0 1-.25 1z"/></svg>
      614 295 8837
    </div>
    <div class="contact__row">
      <svg viewBox="0 0 24 24"><path d="M7 1h10a2 2 0 0 1 2 2v18a2 2 0 0 1-2 2H7a2 2 0 0 1-2-2V3a2 2 0 0 1 2-2zm0 3v14h10V4zm5 15.5a1 1 0 1 0 0 2 1 1 0 0 0 0-2z"/></svg>
      872 531 4406
    </div>
  </div>

  <div class="contact contact--office">
    <div class="contact__row">
      <svg viewBox="0 0 24 24"><path d="M6 2h10v6H6zM3 9h18a1 1 0 0 1 1 1v8h-4v4H6v-4H2v-8a1 1 0 0 1 1-1zm5 7v4h8v-4z"/></svg>
      457 210 6693
    </div>
    <div class="contact__row">
      <svg viewBox="0 0 24 24"><path d="M2 5h20v14H2zm2 2v.5l8 5 8-5V7zm0 3v7h16v-7l-8 5z"/></svg>
      mail@rankelco.com
    </div>
  </div>
</section>

</body>
</html>
```